Los Brava Dip – CPG Website with WordPress - Store Locator: WP Maps plugin

Larkfield Food Company is a startup consumer packaged goods (CPG) brand launching its flagship product line — Los Brava Dip. We’re seeking a talented web designer to create a bold, professional, mobile-optimized website using WordPress with a WP Maps store locator to help customers find local retailers.

Our goal is to build a strong online presence that supports both retail growth and direct-to-consumer sales.

See Los Brava _Website_Design_Brief word document.

The website URL is https://losbravadip.example/

Target Market(s)

Consumers of gourmet salsa

Industry/Entity Type

Consumer Packaged Goods - Salsa manufacturer.

Coding

Coded - Design and coding required

Number of Pages Required

5+ page

Requirements
Must have
• The design of the Los Brava Dip website shall emulate the clean, polished aesthetic of Fennigo.example.

```html
<!DOCTYPE html>
<html lang="en">
<head>
<meta charset="utf-8">
<title>Los Brava Dip</title>
<link href="https://fonts.googleapis.com/css2?family=Jost:wght@400;500;600&family=Roboto+Slab:wght@500&display=swap" rel="stylesheet">
<style>
:root{
  --red:#c8452a;
  --red-line:#e07a7a;
  --green:#3a6b25;
  --yellow:#f6bb3c;
  --yellow-deep:#b9862a;
  --ink:#1d1d1d;
  --muted:#444;
  --white:#fff;
  --teal:#0f8a6a;
}
*{margin:0;padding:0;box-sizing:border-box}
html,body{width:1200px;height:3157px;overflow:hidden;background:var(--white)}
body{position:relative;font-family:"Jost",sans-serif;color:var(--ink)}
.abs{position:absolute}
/* nav */
.nav a{position:absolute;top:29px;font-size:14px;letter-spacing:1px;color:var(--ink);text-decoration:none;font-weight:500}
.brand{position:absolute;font-weight:600;color:var(--red);white-space:nowrap}
.nav .brand{left:532px;top:14px;font-size:38px;line-height:48px}
.btn-contact{position:absolute;left:976px;top:21px;width:130px;height:34px;background:var(--red);color:var(--white);font-size:14px;letter-spacing:1px;display:flex;align-items:center;justify-content:center;font-weight:500}
/* hero */
.hero{left:0;top:78px;width:1200px;height:613px;background:var(--red);overflow:hidden}
.hero-bowl{left:-20px;top:0;width:640px;height:613px;background:radial-gradient(circle at 45% 45%,#e2361c 0,#c92d18 45%,#8a5a35 70%,#6b4b2e 100%)}
.hero-jar{background:linear-gradient(160deg,#d9b85b,#d8402b 45%,#a82a1a)}
.hero-rule{left:592px;width:499px;height:1px;background:#e9b7a8}
.hero-title{position:absolute;left:592px;width:499px;text-align:center;color:var(--white);font-size:40px;font-weight:600;line-height:58px;letter-spacing:0;white-space:nowrap}
.btn-outline{position:absolute;display:flex;align-items:center;justify-content:center;font-size:14px;letter-spacing:1.2px;font-weight:500;border:2px solid;white-space:nowrap}
.btn-shop{left:773px;top:392px;width:159px;height:42px;color:var(--white);border-color:var(--white)}
/* section titles */
.rule{height:1.5px}
.sec-title{position:absolute;left:0;width:1200px;text-align:center;font-size:34px;font-weight:600;letter-spacing:.5px;white-space:nowrap}
/* featured */
.feature-jars{left:116px;top:913px;width:442px;height:294px;background:linear-gradient(90deg,#d6452c 0 32%,#8fb848 32% 66%,#e6702e 66%);border-radius:28px 28px 40px 40px}
.feature-name{left:651px;top:936px;font-family:"Roboto Slab",serif;font-size:34px;font-weight:500;color:var(--ink);white-space:nowrap}
.feature-text{left:651px;top:995px;width:450px;font-size:18px;line-height:27px;color:var(--muted)}
.btn-view{left:653px;top:1162px;width:182px;height:43px;color:var(--red);border-color:var(--red)}
/* reviews */
.reviews{left:0;top:1329px;width:1200px;height:633px;background:var(--green)}
.review-box{left:107px;top:1502px;width:996px;height:386px;border:2px solid var(--yellow);box-shadow:7px 8px 0 var(--yellow)}
.review-lead{left:0;top:1548px;width:1200px;text-align:center;color:var(--white);font-size:22px;font-weight:500;white-space:nowrap}
.review-lead small{font-size:17px}
.review-card{top:1618px;width:291px;height:180px;background:var(--white);padding:28px 34px}
.review-card h3{font-size:16px;font-weight:500;margin:10px 0 4px}
.review-card p{font-size:12.5px;line-height:19px;color:var(--muted)}
.review-card strong{display:block;margin-top:10px;font-size:14px;font-weight:600}
.stars{display:flex;gap:2px}
.stars span{width:15px;height:15px;background:var(--teal)}
/* recipes */
.recipes{left:0;top:1962px;width:1200px;height:697px;background:var(--yellow)}
.recipe-card{left:112px;top:2139px;width:995px;height:434px;background:var(--white);border:1.5px solid var(--ink);box-shadow:7px 8px 0 var(--yellow-deep)}
.recipe-photo{left:145px;top:2165px;width:441px;height:376px;background:radial-gradient(ellipse at 55% 60%,#e9a96b 0,#d88b4f 35%,#2f4fa0 60%,#1c3478 100%)}
.recipe-title{left:662px;top:2206px;font-size:25px;font-weight:600;line-height:29px;letter-spacing:.5px;white-space:nowrap}
.recipe-dash{left:662px;top:2271px;width:34px;height:2px;background:var(--red)}
.recipe-text{left:661px;top:2286px;width:400px;font-size:15.5px;line-height:27px;color:var(--muted)}
.btn-recipe{left:659px;top:2442px;width:159px;height:42px;color:var(--red);border-color:var(--red)}
/* instagram */
.insta{left:0;top:2659px;width:1200px;height:142px;background:var(--red)}
/* footer */
.foot-brand{left:129px;top:2886px;font-size:46px;line-height:56px}
.social{top:2981px;width:36px;height:36px;border-radius:50%}
.foot-head{position:absolute;top:2858px;font-size:21px;font-weight:600;letter-spacing:.5px;padding-top:4px;border-top:2px solid var(--red);white-space:nowrap}
.foot-list{position:absolute;list-style:none;font-size:16px;line-height:28.5px;color:var(--ink);white-space:nowrap}
.foot-mail{left:833px;top:2904px;font-size:18px;white-space:nowrap}
.copy{left:0;top:3101px;width:1200px;text-align:center;font-size:13px;color:var(--muted)}
</style>
</head>
<body>

<header class="nav">
  <a style="left:102px">ABOUT</a>
  <a style="left:206px">PRODUCTS</a>
  <a style="left:341px">WHERE TO BUY</a>
  <span class="brand">Los Brava</span>
  <a style="left:750px">RECIPES</a>
  <a style="left:865px">REVIEW</a>
  <span class="btn-contact">CONTACT ›</span>
</header>

<section class="abs hero">
  <div class="abs hero-bowl" role="img" aria-label="Bowl of tomato salsa with fresh herbs on a wooden board"></div>
  <div class="abs hero-jar" role="img" aria-label="Los Brava salsa jar" style="left:1075px;top:30px;width:140px;height:200px;transform:rotate(35deg)"></div>
  <div class="abs hero-jar" role="img" aria-label="Los Brava habanero salsa jar" style="left:640px;top:440px;width:170px;height:230px;transform:rotate(18deg)"></div>
  <div class="abs" role="img" aria-label="Los Brava verde salsa jar" style="left:995px;top:420px;width:170px;height:230px;transform:rotate(-35deg);background:linear-gradient(160deg,#d9b85b,#8fb848 45%,#5e8a2c)"></div>
  <div class="abs hero-rule" style="top:182px"></div>
  <h1 class="hero-title" style="top:186px">SPICE UP YOUR MEALS!</h1>
  <div class="abs hero-rule" style="top:243px"></div>
  <p class="hero-title" style="top:244px">WITH LOS BRAVA</p>
  <span class="btn-outline btn-shop" style="top:314px">SHOP NOW ›</span>
</section>

<section>
  <div class="abs rule" style="left:88px;top:765px;width:995px;background:var(--red-line)"></div>
  <h2 class="sec-title" style="top:776px">FEATURED PRODUCT</h2>
  <div class="abs rule" style="left:88px;top:832px;width:995px;background:var(--red-line)"></div>
  <div class="abs feature-jars" role="img" aria-label="Three Los Brava salsa jars: habanero, verde and all natural"></div>
  <h3 class="abs feature-name">Los Brava multi Pack</h3>
  <p class="abs feature-text">Lorem ipsum dolor sit amet, consectetur adipiscing elit, sed do eiusmod tempor Ancididunt ut labore et dolore magna aliqua. Quis ipsum suspendisse ultrices gravida. Risus commodo viverra maecenas accumsan lacus vel facilisis.</p>
  <span class="btn-outline btn-view">VIEW PRODUCTS</span>
</section>

<section class="abs reviews"></section>
<div class="abs rule" style="left:98px;top:1391px;width:994px;background:#e8e8e8"></div>
<h2 class="sec-title" style="top:1401px;color:var(--white)">REVIEWS</h2>
<div class="abs rule" style="left:98px;top:1459px;width:994px;background:#e8e8e8"></div>
<div class="abs review-box"></div>
<p class="abs review-lead">Let Customer Speak for us <span style="color:#2aa0d8;font-size:17px;letter-spacing:2px">★★★★★</span> <small>from 448 reviews</small></p>

<article class="abs review-card" style="left:161px">
  <div class="stars"><span></span><span></span><span></span><span></span><span></span></div>
  <h3>Awesome taste, fresh</h3>
  <p>Lorem ipsum dolor sit amet, consectetur adipiscing elit, sed do eiusmod temp</p>
  <strong>Dara Quill</strong>
</article>
<article class="abs review-card" style="left:472px">
  <div class="stars"><span></span><span></span><span></span><span></span><span></span></div>
  <h3>Awesome taste, fresh</h3>
  <p>Lorem ipsum dolor sit amet, consectetur adipiscing elit, sed do eiusmod temp</p>
  <strong>Dara Quill</strong>
</article>
<article class="abs review-card" style="left:780px">
  <div class="stars"><span></span><span></span><span></span><span></span><span></span></div>
  <h3>Awesome taste, fresh</h3>
  <p>Lorem ipsum dolor sit amet, consectetur adipiscing elit, sed do eiusmod temp</p>
  <strong>Dara Quill</strong>
</article>
<svg class="abs" style="left:580px;top:1814px" width="64" height="30" viewBox="0 0 64 30" fill="none" stroke="#cfd8c8" stroke-width="3">
  <polyline points="18,3 8,15 18,27"/><polyline points="46,3 56,15 46,27"/>
</svg>

<section class="abs recipes"></section>
<div class="abs rule" style="left:113px;top:2026px;width:994px;background:var(--ink)"></div>
<h2 class="sec-title" style="top:2036px">RECIPES</h2>
<div class="abs rule" style="left:113px;top:2094px;width:994px;background:var(--ink)"></div>
<div class="abs recipe-card"></div>
<div class="abs recipe-photo" role="img" aria-label="Baked chicken with salsa and melted cheese on a blue plate with cilantro"></div>
<h3 class="abs recipe-title">BAKED CHICKEN WITH<br>SALSA AND SOUR CREAM</h3>
<div class="abs recipe-dash"></div>
<p class="abs recipe-text">Looking for a weeknight dinner that's both effortless and packed with flavor? This Baked Chicken with Salsa and Sour Cream is a creamy, cheesy, oven-baked comfort dish that's as satisfying as it is simple. Seasoned with taco spices</p>
<span class="btn-outline btn-recipe">VIEW RECIPE</span>
<svg class="abs" style="left:985px;top:2476px" width="64" height="30" viewBox="0 0 64 30" fill="none" stroke="#9a9a9a" stroke-width="2.5">
  <polyline points="18,3 8,15 18,27"/><polyline points="46,3 56,15 46,27"/>
</svg>

<section class="abs insta"></section>
<div class="abs rule" style="left:109px;top:2699px;width:995px;background:#ecc0b3"></div>
<h2 class="sec-title" style="top:2708px;color:var(--white);font-size:30px;left:8px">FOLLOW US ON INSTAGRAM</h2>
<div class="abs rule" style="left:109px;top:2766px;width:995px;background:#ecc0b3"></div>

<footer>
  <span class="brand foot-brand">Los Brava</span>
  <span class="abs social" style="left:174px;background:var(--red)" aria-label="Social profile"></span>
  <span class="abs social" style="left:228px;border:2.5px solid var(--ink);width:32px;height:32px;top:2983px" aria-label="Social profile"></span>
  <h4 class="foot-head" style="left:396px">NAVIGATION</h4>
  <ul class="foot-list" style="left:396px;top:2898px">
    <li>About Us</li><li>Products</li><li>Recipes</li><li>Reviews</li>
  </ul>
  <ul class="foot-list" style="left:555px;top:2902px">
    <li>Privacy Policy</li><li>Shipping Policy</li><li>Terms and Conditions</li><li>Contact us</li>
  </ul>
  <h4 class="foot-head" style="left:795px">CONTACT US</h4>
  <svg class="abs" style="left:795px;top:2903px" width="30" height="30" viewBox="0 0 30 30">
    <circle cx="15" cy="15" r="15" fill="#2b2b2b"/>
    <rect x="8" y="10" width="14" height="10" fill="none" stroke="#fff" stroke-width="1.5"/>
    <polyline points="8,10 15,16 22,10" fill="none" stroke="#fff" stroke-width="1.5"/>
  </svg>
  <span class="abs foot-mail">support@losbravadip.example</span>
  <div class="abs rule" style="left:0;top:3079px;width:1200px;background:#cfcfcf;height:1px"></div>
  <p class="abs copy">Copyright © 2025 Brightloop.&nbsp; All Right Reserved</p>
</footer>

</body>
</html>
```